Simple Logo Design for Semi-Clear Plastic Frosted Card stock

Create a business card on frosted plastic. compliment existing logo elements with a tree trunk, roots, or seed at the lower half and the full logo both on the front.

Contact information will go on a solid portion of the back of this design since this card stock is semi-transparent.

It is important to consider this plastic card stock medium in your design. I found helpful tips and guides listed at vellaprint-sample.net: be careful to understand ink printed on plastic cards cannot have too much of a consistent print area or risks peeling and fine lines can easily scratch off.
Updates

2" x 3.5" 20PT Clear Plastic Business cards with Round corners Please get info or templates here: https://www.vellaprint-sample.net/product-detail/2-x-35-20pt-clear-plastic-business-cards-with-round-corners

Target Market(s)

Not for profit- religion

Industry/Entity Type

Business

Must include complementary elements to the existing logo

Font styles to use
Decorative

Colors
000000

Requirements
Must have
• Elements of community, nature and oneness. Such as: seed, roots, tree trunk, etc.
• Three lines of space on the back for Name, Title, Phone Number.
Nice to have
• I like a light use of decorative elements
Should not have
• No eyes, from faces or animals.

```html
<!DOCTYPE html>
<html lang="en">
<head>
<meta charset="utf-8">
<title>Steadfast Grove – Frosted Business Card</title>
<link rel="stylesheet" href="https://fonts.googleapis.com/css2?family=Fira+Sans:wght@400;500&display=swap">
<style>
  :root {
    --backdrop: #e7e3de;
    --teal-deep: #123f3d;
    --teal-mid: #2b5f5c;
    --leaf-green: #2f6a2a;
    --leaf-dark: #1f4a1d;
    --frost-light: #f1f2f1;
    --frost-mid: #d9dcdb;
    --ink-white: #ffffff;
    --ink-soft: #d7e3e1;
    --brand-green: #1f5a22;
  }
  html, body {
    margin: 0;
    padding: 0;
    width: 1200px;
    height: 969px;
    overflow: hidden;
    background: var(--backdrop);
  }
  .canvas {
    position: relative;
    width: 1200px;
    height: 969px;
  }
  .business-card {
    position: absolute;
    left: 100px;
    top: 199px;
    width: 1000px;
    height: 571px;
    border-radius: 30px;
    overflow: hidden;
    box-shadow: 0 18px 40px rgba(0, 0, 0, 0.18);
  }
  .card-art {
    position: absolute;
    inset: 0;
    width: 100%;
    height: 100%;
  }
  .contact-block {
    position: absolute;
    left: 62px;
    top: 196px;
    font-family: "Fira Sans", sans-serif;
    color: var(--ink-white);
  }
  .contact-name {
    margin: 0;
    font-size: 38px;
    font-weight: 500;
    letter-spacing: 1px;
    line-height: 1.1;
  }
  .contact-title {
    margin: 8px 0 0;
    font-size: 30px;
    font-weight: 400;
    letter-spacing: 1px;
    color: var(--ink-soft);
  }
  .contact-phone {
    margin: 26px 0 0;
    font-size: 32px;
    font-weight: 400;
    letter-spacing: 1px;
    color: var(--ink-soft);
  }
  .brand-lockup {
    position: absolute;
    left: 560px;
    top: 270px;
    width: 400px;
    display: flex;
    align-items: center;
    justify-content: center;
    gap: 16px;
  }
  .brand-dot {
    width: 34px;
    height: 34px;
    border-radius: 50%;
    background: var(--brand-green);
    flex: none;
  }
  .brand-name {
    font-family: "Fira Sans", sans-serif;
    font-weight: 500;
    font-size: 46px;
    letter-spacing: 1px;
    color: var(--brand-green);
    text-transform: uppercase;
    white-space: nowrap;
  }
</style>
</head>
<body>
<main class="canvas">
  <section class="business-card">
    <svg class="card-art" viewBox="0 0 1000 571" preserveAspectRatio="none" aria-hidden="true">
      <defs>
        <linearGradient id="tealPanel" x1="0" y1="0" x2="1" y2="1">
          <stop offset="0" stop-color="var(--teal-deep)"/>
          <stop offset="0.55" stop-color="var(--teal-mid)"/>
          <stop offset="1" stop-color="var(--teal-deep)"/>
        </linearGradient>
        <linearGradient id="leafSweep" x1="0" y1="0" x2="1" y2="1">
          <stop offset="0" stop-color="var(--leaf-green)"/>
          <stop offset="1" stop-color="var(--leaf-dark)"/>
        </linearGradient>
        <radialGradient id="frostFace" cx="0.55" cy="0.45" r="0.6">
          <stop offset="0" stop-color="var(--frost-light)"/>
          <stop offset="1" stop-color="var(--frost-mid)"/>
        </radialGradient>
      </defs>
      <rect class="teal-panel" width="1000" height="571" fill="url(#tealPanel)"/>
      <circle class="leaf-sweep" cx="738" cy="330" r="345" fill="url(#leafSweep)"/>
      <circle class="sweep-edge" cx="760" cy="300" r="353" fill="var(--ink-white)" opacity="0.85"/>
      <circle class="frosted-face" cx="760" cy="300" r="350" fill="url(#frostFace)"/>
    </svg>

    <div class="contact-block">
      <p class="contact-name">MARA ELLISON</p>
      <p class="contact-title">PRESIDENT</p>
      <p class="contact-phone">555 0142 7781</p>
    </div>

    <div class="brand-lockup">
      <span class="brand-dot"></span>
      <span class="brand-name">Steadfast Grove</span>
    </div>
  </section>
</main>
</body>
</html>
```